Food Hall in San Clemente, CA by the Pacific Ocean that has 15 vendors and 2 bars

We need a web page design that highlights our food hall in San Clemente, CA. The name of the food hall is Calloway Food Hall. Inside of the food hall there are 15 different vendors and 2 bars. The place has a beautiful patio and it is by Pacific Ocean. Most of the vendors are local to San Clemente area. The highly anticipated location is opening during the summer of 2025. Website should have a dropdown menu for the different vendors that are in the food hall and people should be able to click to their respective business website. The website should also include link to our social media channels and also a link to provide comments and subscribe for the mailing list.
Target Market(s)
Mostly residents in the San Clemente, CA and surrounding areas. Couples, families and tourist alike that are looking for an exceptional dining experience that everyone can find something they like.
Industry/Entity Type
Restaurants
Coding
Number of Pages Required
Font styles to use
Look and feel

```html
<!DOCTYPE html>
<html lang="en">
<head>
<meta charset="utf-8">
<title>Calloway Food Hall · San Clemente, CA</title>
<link href="https://fonts.googleapis.com/css2?family=Playfair+Display:wght@600;700&family=Poppins:wght@400;500;600&display=swap" rel="stylesheet">
<style>
:root{
  --navy:#1e3d7a;
  --navy-deep:#1c3874;
  --ink:#1b1f2a;
  --dark:#1d2230;
  --sky:#dff1f8;
  --paper:#ffffff;
  --mist:#f1f1f1;
  --text:#2b2b2b;
  --muted:#555b66;
  --teal:#57afd0;
  --line:#b9bec6;
}
*{box-sizing:border-box;margin:0;padding:0}
html,body{width:1200px;height:4967px;overflow:hidden}
body{font-family:"Poppins",sans-serif;color:var(--text);background:var(--paper);font-size:15px}
section,header,nav,footer,article{position:relative;width:1200px}
article{width:auto}
a{color:inherit;text-decoration:none}

/* top bar */
.topbar{height:70px;background:var(--dark);color:#fff;font-size:14px}
.topbar .item{position:absolute;top:24px;display:flex;align-items:center;gap:10px;white-space:nowrap}
/* nav */
.nav{height:93px;background:var(--sky)}
.brand{position:absolute;left:112px;top:22px;font-family:"Playfair Display",serif;font-weight:600;font-size:34px;line-height:44px;color:var(--navy);white-space:nowrap}
.menu{position:absolute;top:36px;font-size:16px;line-height:22px;color:var(--ink);font-weight:500;display:flex;align-items:center;gap:6px;white-space:nowrap}
.menu.home{left:484px;top:25px;width:94px;height:40px;background:var(--navy);color:#fff;justify-content:center}
/* hero */
.hero{height:553px;background:radial-gradient(ellipse at 30% 40%,#6b4a2c 0%,#3a2c24 45%,#1c1c20 100%);color:#fff;text-align:center}
.hero .kicker{position:absolute;top:160px;width:100%;font-weight:600;font-size:15px}
.hero h1{position:absolute;top:196px;left:120px;width:960px;font-family:"Playfair Display",serif;font-size:42px;line-height:55px;font-weight:700}
.hero p{position:absolute;top:333px;left:250px;width:700px;font-size:16px;line-height:25px}
.btn{position:absolute;display:flex;align-items:center;justify-content:center;font-size:16px;font-weight:500}
.btn.solid{background:var(--navy);color:#fff}
.btn.ghost{border:2px solid #fff;color:#fff}
/* common headings */
.kick{position:absolute;font-size:15px;font-weight:500;color:var(--ink)}
.h2{position:absolute;font-family:"Playfair Display",serif;font-weight:700;font-size:34px;line-height:45px;color:var(--ink)}
.para{position:absolute;font-size:16px;line-height:27px;color:var(--ink)}
.photo{position:absolute;border-radius:6px;box-shadow:0 4px 10px rgba(0,0,0,.35)}
.divider{position:absolute;height:1px;background:var(--line)}
.stat{position:absolute;display:flex;align-items:center;gap:16px;font-family:"Playfair Display",serif;font-weight:700;font-size:19px;color:var(--ink)}
.stat .ico{width:52px;height:52px;background:var(--navy);display:flex;align-items:center;justify-content:center;border-radius:3px}
/* vendors */
.vendors{height:589px;background:var(--sky)}
.card{position:absolute;top:189px;width:228px;height:315px;background:#fff;box-shadow:0 2px 6px rgba(0,0,0,.2)}
.card .media{height:183px;display:flex;align-items:center;justify-content:center;text-align:center}
.card .desc{padding:18px 12px 0;font-size:13.5px;line-height:24px;color:var(--ink)}
.link{display:flex;align-items:center;gap:10px;color:var(--navy);font-size:16px;font-weight:500}
.card .link{position:absolute;left:12px;top:267px}
.arrow{position:absolute;width:42px;height:42px;border-radius:50%;background:#8a8f96;display:flex;align-items:center;justify-content:center}
/* why */
.why{height:590px;background:var(--sky)}
.feature{position:absolute;left:116px;display:flex;align-items:center;gap:20px;font-family:"Playfair Display",serif;font-weight:600;font-size:16px;color:var(--ink)}
.tile{position:absolute;border-radius:5px;display:flex;align-items:flex-end;justify-content:center;padding-bottom:22px;color:#fff;font-family:"Playfair Display",serif;font-weight:600;font-size:16px}
/* taste */
.taste{height:565px;background:linear-gradient(180deg,#8a7d72 0%,#c7c1bb 30%,#d8d4cf 70%,#b4a99f 100%);text-align:center}
.taste .veil{position:absolute;inset:0;background:rgba(230,236,240,.55)}
/* newsletter */
.news{height:315px;background:var(--navy-deep);color:#fff;text-align:center}
.news h2{position:absolute;top:78px;width:100%;font-family:"Playfair Display",serif;font-weight:700;font-size:34px}
.news p{position:absolute;top:143px;width:100%;font-size:16px;font-weight:500}
.news .field{position:absolute;left:416px;top:208px;width:252px;height:34px;background:#fff;color:#333;font-size:13px;text-align:left;padding:8px 22px}
.news .sub{position:absolute;left:677px;top:208px;width:108px;height:34px;border:1px solid #fff;font-size:13px;font-weight:600;display:flex;align-items:center;justify-content:center}
/* blogs */
.blogs{height:672px;background:var(--mist)}
.post{position:absolute;top:195px;width:312px}
.post .media{height:215px;border-radius:5px;box-shadow:0 3px 8px rgba(0,0,0,.3)}
.post .date{margin-top:30px;font-size:13px;display:flex;align-items:center;gap:8px;color:var(--ink)}
.post .date::after{content:"";width:56px;height:2px;background:var(--navy)}
.post h3{margin-top:10px;font-family:"Playfair Display",serif;font-weight:600;font-size:16px;color:var(--navy)}
.post .desc{margin-top:6px;font-size:13.5px;line-height:27px;color:var(--ink)}
.post .link{margin-top:14px}
/* footer */
.footer{height:390px;background:var(--dark);color:#fff;text-align:center}
.footer .logo{position:absolute;top:58px;width:100%;font-family:"Playfair Display",serif;font-weight:600;font-size:42px;color:var(--teal)}
.footer .tag{position:absolute;top:148px;width:100%;font-size:16px;font-weight:500}
.footer .contact{position:absolute;top:185px;width:100%;display:flex;justify-content:center;gap:26px;font-size:15px}
.footer .contact span{display:flex;align-items:center;gap:10px}
.footer .links{position:absolute;top:232px;width:100%;font-size:16px;font-weight:500}
.footer .rule{position:absolute;top:280px;left:112px;width:976px;height:1px;background:#6c717c}
.footer .copy{position:absolute;top:308px;width:100%;font-size:16px;font-weight:500}
</style>
</head>
<body>

<header class="topbar">
  <div class="item" style="left:112px">
    <svg width="16" height="16" viewBox="0 0 24 24" fill="#fff"><path d="M6.6 10.8a15 15 0 0 0 6.6 6.6l2.2-2.2a1 1 0 0 1 1-.25 11 11 0 0 0 3.6.6 1 1 0 0 1 1 1V20a1 1 0 0 1-1 1A17 17 0 0 1 3 4a1 1 0 0 1 1-1h3.5a1 1 0 0 1 1 1c0 1.25.2 2.45.6 3.6a1 1 0 0 1-.25 1z"/></svg>
    Calloway Food Hall · San Clemente, CA
  </div>
  <div class="item" style="left:622px">
    <svg width="16" height="16" viewBox="0 0 24 24" fill="#fff"><path d="M6.6 10.8a15 15 0 0 0 6.6 6.6l2.2-2.2a1 1 0 0 1 1-.25 11 11 0 0 0 3.6.6 1 1 0 0 1 1 1V20a1 1 0 0 1-1 1A17 17 0 0 1 3 4a1 1 0 0 1 1-1h3.5a1 1 0 0 1 1 1c0 1.25.2 2.45.6 3.6a1 1 0 0 1-.25 1z"/></svg>
    (555) 014-2025
  </div>
  <div class="item" style="left:818px">
    <svg width="20" height="16" viewBox="0 0 24 18" fill="none" stroke="#fff" stroke-width="2"><rect x="1" y="1" width="22" height="16"/><path d="M1 1l11 9 11-9"/></svg>
    hello@callowayfoodhall.com
  </div>
</header>

<nav class="nav">
  <div class="brand">Calloway Food Hall</div>
  <a class="menu home">Home</a>
  <a class="menu" style="left:620px">About</a>
  <a class="menu" style="left:738px">Vendors <svg width="10" height="8" viewBox="0 0 10 8"><path d="M1 2l4 4 4-4" fill="none" stroke="#1b1f2a" stroke-width="1.5"/></svg></a>
  <a class="menu" style="left:892px">Contact Us</a>
  <a class="menu" style="left:1045px">Blogs</a>
</nav>

<section class="hero" role="img" aria-label="Warm evening interior of the food hall with seating and large windows">
  <div class="kicker">Welcome to Calloway Food Hall</div>
  <h1>15 Artisanal Eateries. 2 Buzzing Bars. 1 Beautiful Coastal Destination.</h1>
  <p>A brand new food hall experience in the heart of San Clemente, CA — opening Summer 2025.</p>
  <a class="btn solid" style="left:373px;top:420px;width:215px;height:54px">Meet Our Vendors</a>
  <a class="btn ghost" style="left:612px;top:420px;width:217px;height:54px">Meet Our Vendors</a>
</section>

<section class="about" style="height:580px">
  <div class="photo" role="img" aria-label="Coastal street view with a palm tree" style="left:112px;top:88px;width:312px;height:340px;background:linear-gradient(160deg,#b9c6cf,#8a8378 60%,#5c4a3c)"></div>
  <div class="photo" role="img" aria-label="Food hall building facade lit at dusk" style="left:206px;top:170px;width:272px;height:322px;background:linear-gradient(180deg,#5a6fa8 0%,#8c7fa3 45%,#3b3035 75%,#c7883e 100%)"></div>
  <div class="kick" style="left:522px;top:90px">About Us</div>
  <div class="h2" style="left:518px;top:126px;width:560px">A Culinary Destination by the Pacific</div>
  <div class="para" style="left:518px;top:228px;width:572px">Located just steps from the ocean, Calloway Food Hall brings together a curated collection of 15 diverse, locally inspired vendors and 2 vibrant bars — all under one roof. With indoor-outdoor seating, a breezy coastal patio, and something for every craving, Calloway is your new go-to for everything from casual bites to craft cocktails.</div>
  <div class="divider" style="left:518px;top:414px;width:546px"></div>
  <div class="stat" style="left:522px;top:439px"><span class="ico"><svg width="28" height="28" viewBox="0 0 24 24" fill="none" stroke="#fff" stroke-width="1.6"><rect x="3" y="4" width="18" height="16"/><path d="M3 8h18M7 16h10M8 12h8"/></svg></span>15 Vendors</div>
  <div class="stat" style="left:743px;top:439px"><span class="ico"><svg width="28" height="28" viewBox="0 0 24 24" fill="none" stroke="#fff" stroke-width="1.6"><path d="M5 4h14l-7 8zM12 12v8M8 20h8"/></svg></span>2 Bars</div>
</section>

<section class="vendors">
  <div class="kick" style="left:0;width:1200px;text-align:center;top:80px">Something for Every Taste</div>
  <div class="h2" style="left:0;width:1200px;text-align:center;top:116px">Meet Our Vendors</div>
  <div class="arrow" style="left:34px;top:269px"><svg width="14" height="14" viewBox="0 0 14 14"><path d="M9 2L4 7l5 5" fill="none" stroke="#fff" stroke-width="2"/></svg></div>
  <div class="arrow" style="left:1124px;top:264px"><svg width="14" height="14" viewBox="0 0 14 14"><path d="M5 2l5 5-5 5" fill="none" stroke="#fff" stroke-width="2"/></svg></div>

  <div class="card" style="left:112px">
    <div class="media" style="background:#000;color:#fff;font-weight:600;font-size:20px">Ember Hot Chicken</div>
    <div class="desc">Lorem Ipsum is simply dummy text of the printing</div>
    <a class="link">Visit Website <svg width="20" height="20" viewBox="0 0 20 20" fill="none" stroke="#1e3d7a" stroke-width="1.5"><circle cx="10" cy="10" r="8.5"/><path d="M7 13l6-6M8 7h5v5"/></svg></a>
  </div>
  <div class="card" style="left:361px">
    <div class="media" style="background:#c9c9c9;color:#1b1f2a;font-weight:600;font-size:20px">Orbit Eats</div>
    <div class="desc">Lorem Ipsum is simply dummy text of the printing</div>
    <a class="link">Visit Website <svg width="20" height="20" viewBox="0 0 20 20" fill="none" stroke="#1e3d7a" stroke-width="1.5"><circle cx="10" cy="10" r="8.5"/><path d="M7 13l6-6M8 7h5v5"/></svg></a>
  </div>
  <div class="card" style="left:610px">
    <div class="media" role="img" aria-label="Food hall building lit at dusk" style="background:linear-gradient(180deg,#5a6fa8,#8c7fa3 45%,#3b3035 75%,#c7883e)"></div>
    <div class="desc">Lorem Ipsum is simply dummy text of the printing</div>
    <a class="link">Visit Website <svg width="20" height="20" viewBox="0 0 20 20" fill="none" stroke="#1e3d7a" stroke-width="1.5"><circle cx="10" cy="10" r="8.5"/><path d="M7 13l6-6M8 7h5v5"/></svg></a>
  </div>
  <div class="card" style="left:859px">
    <div class="media" style="background:#cfcfcf;color:#1b1f2a;font-weight:600;font-size:20px">Dolce Mare Gelato</div>
    <div class="desc">Lorem Ipsum is simply dummy text of the printing</div>
    <a class="link">Visit Website <svg width="20" height="20" viewBox="0 0 20 20" fill="none" stroke="#1e3d7a" stroke-width="1.5"><circle cx="10" cy="10" r="8.5"/><path d="M7 13l6-6M8 7h5v5"/></svg></a>
  </div>
</section>

<section class="bar" style="height:550px">
  <div class="kick" style="left:117px;top:88px">Bar Section</div>
  <div class="h2" style="left:112px;top:123px">Sip &amp; Savor</div>
  <div class="para" style="left:112px;top:192px;width:470px">Our two signature bars serve up everything from craft beers to tropical cocktails. Whether you're here for happy hour or a late-night sip by the ocean breeze, the drinks at Calloway are always worth raising a glass.</div>
  <div class="divider" style="left:112px;top:366px;width:454px"></div>
  <div class="stat" style="left:112px;top:400px"><span class="ico"><svg width="28" height="28" viewBox="0 0 24 24" fill="none" stroke="#fff" stroke-width="1.6"><rect x="3" y="4" width="18" height="16"/><path d="M3 8h18M7 16h10M8 12h8"/></svg></span>15 Vendors</div>
  <div class="stat" style="left:333px;top:400px"><span class="ico"><svg width="28" height="28" viewBox="0 0 24 24" fill="none" stroke="#fff" stroke-width="1.6"><path d="M5 4h14l-7 8zM12 12v8M8 20h8"/></svg></span>2 Bars</div>
  <div class="photo" role="img" aria-label="Cocktail glass on a bar counter with warm bokeh lights" style="left:610px;top:77px;width:478px;height:392px;background:radial-gradient(circle at 38% 48%,#b0602e 0%,#4a2616 30%,#130c0a 70%)"></div>
</section>

<section class="why">
  <div class="kick" style="left:117px;top:85px">Experience the Best</div>
  <div class="h2" style="left:112px;top:120px">Why People Love Us</div>
  <div class="para" style="left:112px;top:183px;width:330px">Lorem Ipsum is simply dummy text of the printing and typesetting industry.</div>
  <div class="feature" style="top:266px"><svg width="30" height="30" viewBox="0 0 24 24" fill="none" stroke="#1b1f2a" stroke-width="1.4"><path d="M3 12h18a9 9 0 0 1-18 0zM8 8c0-2 2-3 4-3s4 1 4 3"/></svg>Vegetarian Delights</div>
  <div class="feature" style="top:321px"><svg width="30" height="30" viewBox="0 0 24 24" fill="none" stroke="#1b1f2a" stroke-width="1.4"><circle cx="12" cy="12" r="8"/><path d="M4 12h16M12 4c3 3 3 13 0 16M12 4c-3 3-3 13 0 16"/></svg>International Flavours</div>
  <div class="feature" style="top:376px"><svg width="30" height="30" viewBox="0 0 24 24" fill="none" stroke="#1b1f2a" stroke-width="1.4"><path d="M3 13h18a9 8 0 0 1-18 0zM12 9c0-3 2-5 5-5 0 3-2 5-5 5z"/></svg>Healthy Eats</div>
  <a class="btn solid" style="left:117px;top:440px;width:215px;height:53px;box-shadow:0 3px 6px rgba(0,0,0,.3)">View Entire Menus</a>
  <div class="tile" role="img" aria-label="Roasted dish on a dark plate" style="left:485px;top:83px;width:270px;height:196px;background:radial-gradient(circle at 50% 45%,#7a4a26,#22160f 70%)">Special Menu</div>
  <div class="tile" role="img" aria-label="Iced cocktail with lime" style="left:485px;top:298px;width:270px;height:192px;background:radial-gradient(circle at 50% 50%,#4c5a40,#141714 70%)">Drink Menu</div>
  <div class="tile" role="img" aria-label="Spread of seasonal dishes on a table" style="left:776px;top:83px;width:312px;height:407px;background:linear-gradient(180deg,#2a2c24,#5b6034 40%,#6e4a2a 75%,#2a1c14)">Seasonal Menu</div>
</section>

<section class="taste" role="img" aria-label="Blurred dining table backdrop">
  <div class="veil"></div>
  <div class="kick" style="left:0;width:1200px;top:90px">Savor the Flavor</div>
  <div class="h2" style="left:0;width:1200px;top:124px">Taste Our Best</div>
  <div class="para" style="left:225px;width:750px;top:172px;font-size:16px;line-height:25px">Opening in Summer 2025, we're excited to welcome food lovers, families, couples, and travelers alike to enjoy San Clemente's newest gathering space.</div>
  <div class="tile" role="img" aria-label="Couple dining together" style="left:112px;top:265px;width:312px;height:215px;background:linear-gradient(135deg,#3b4a5c,#6b5440 60%,#2a2420)">Couples</div>
  <div class="tile" role="img" aria-label="Family sharing a meal outdoors" style="left:444px;top:265px;width:312px;height:215px;background:linear-gradient(135deg,#4d5a3a,#7a5a3a 60%,#2e2a22)">Families</div>
  <div class="tile" role="img" aria-label="Group of travelers dining" style="left:776px;top:265px;width:312px;height:215px;background:linear-gradient(135deg,#3a3a40,#7a6a5a 55%,#2a3550)">Touristers</div>
</section>

<section class="news">
  <h2>Subscribe to&nbsp; Our Newsletter</h2>
  <p>Join our newsletter for the latest updates and insights!</p>
  <div class="field">Enter your Email</div>
  <a class="sub">Subscribe</a>
</section>

<section class="blogs">
  <div class="kick" style="left:117px;top:88px">Stay Informed, Stay Inspired</div>
  <div class="h2" style="left:112px;top:122px">Recent News and Blogs</div>
  <div class="arrow" style="left:34px;top:269px"><svg width="14" height="14" viewBox="0 0 14 14"><path d="M9 2L4 7l5 5" fill="none" stroke="#fff" stroke-width="2"/></svg></div>
  <div class="arrow" style="left:1124px;top:264px"><svg width="14" height="14" viewBox="0 0 14 14"><path d="M5 2l5 5-5 5" fill="none" stroke="#fff" stroke-width="2"/></svg></div>
  <article class="post" style="left:112px">
    <div class="media" role="img" aria-label="Grilled cheese sandwich" style="background:radial-gradient(circle at 50% 50%,#d89a3a,#5a2e14 75%)"></div>
    <div class="date">March 15, 2025</div>
    <h3>Explore Taste Of Beef Rib With Cheese</h3>
    <div class="desc">Lorem Ipsum is simply dummy text of the printing and typesetting industry.</div>
    <a class="link">Read More <svg width="20" height="20" viewBox="0 0 20 20" fill="none" stroke="#1e3d7a" stroke-width="1.5"><circle cx="10" cy="10" r="8.5"/><path d="M7 13l6-6M8 7h5v5"/></svg></a>
  </article>
  <article class="post" style="left:444px">
    <div class="media" role="img" aria-label="Roasted poultry on a dark grill" style="background:radial-gradient(circle at 50% 50%,#8a5228,#1a120c 70%)"></div>
    <div class="date">March 18, 2025</div>
    <h3>High Protein Nutrition Rich Foods</h3>
    <div class="desc">Lorem Ipsum is simply dummy text of the printing and typesetting industry.</div>
    <a class="link">Read More <svg width="20" height="20" viewBox="0 0 20 20" fill="none" stroke="#1e3d7a" stroke-width="1.5"><circle cx="10" cy="10" r="8.5"/><path d="M7 13l6-6M8 7h5v5"/></svg></a>
  </article>
  <article class="post" style="left:776px">
    <div class="media" role="img" aria-label="Dinner table set on a yacht deck" style="background:linear-gradient(180deg,#2b3550,#c88a4a 45%,#e8e0d8 80%)"></div>
    <div class="date">March 25, 2025</div>
    <h3>Rich &amp; Delightful Dinner Menus</h3>
    <div class="desc">Lorem Ipsum is simply dummy text of the printing and typesetting industry.</div>
    <a class="link">Read More <svg width="20" height="20" viewBox="0 0 20 20" fill="none" stroke="#1e3d7a" stroke-width="1.5"><circle cx="10" cy="10" r="8.5"/><path d="M7 13l6-6M8 7h5v5"/></svg></a>
  </article>
</section>

<footer class="footer">
  <div class="logo">Calloway Food Hall</div>
  <div class="tag">Know the signs &amp; Get information to share</div>
  <div class="contact">
    <span><svg width="22" height="16" viewBox="0 0 24 18" fill="none" stroke="#fff" stroke-width="2"><rect x="1" y="1" width="22" height="16"/><path d="M1 1l11 9 11-9"/></svg>hello@callowayfoodhall.com</span>
    <span><svg width="18" height="18" viewBox="0 0 24 24" fill="#fff"><path d="M6.6 10.8a15 15 0 0 0 6.6 6.6l2.2-2.2a1 1 0 0 1 1-.25 11 11 0 0 0 3.6.6 1 1 0 0 1 1 1V20a1 1 0 0 1-1 1A17 17 0 0 1 3 4a1 1 0 0 1 1-1h3.5a1 1 0 0 1 1 1c0 1.25.2 2.45.6 3.6a1 1 0 0 1-.25 1z"/></svg>(555) 014-2025</span>
  </div>
  <div class="links">About Us | Privacy Policy &nbsp;|&nbsp; Vendors &nbsp;| Gallery | Terms and Conditions &nbsp;| Blog &nbsp;| Contact Us</div>
  <div class="rule"></div>
  <div class="copy">Copyright © 2025. Calloway Food Hall · San Clemente, CA.All Rights Reserved</div>
</footer>

</body>
</html>
```